e-commerce store for sport clothing online store "baseball merchandise "web application...

I want to design a UX/UI for my web application website for the online store I will provide you with the following:
1. screen shots of the initial design for the pages>
2. the logo files.
3. The brand guideline file.

the provided files (screen shots) is guideline I want to see CREATIVITY with the UX/UI DESIGN.
PS. PLEASE FOLLOW THE BRANDGUIDE LINE CAREFULLY SPECIALLY THE TYPOGRAPHY & THE COLOR CODES.

PLEASE VISIT THIS WEBSITE brightlane.varomi-qz.com to see more for the screens.

```html
<!DOCTYPE html>
<html lang="en">
<head>
<meta charset="utf-8">
<title>Pitchvale Store – Menu</title>
<link href="https://fonts.googleapis.com/css2?family=Titillium+Web:wght@600;700&family=Lato:wght@400;900&display=swap" rel="stylesheet">
<style>
  :root {
    --navy: #0b1a33;
    --ink: #0f2248;
    --white: #ffffff;
    --page: #f3f3f3;
    --card-border: #d9d9d9;
    --thumb: #eeeeee;
    --accent: #b3002d;
    --scrim: rgba(0, 0, 0, 0.7);
  }
  * { margin: 0; padding: 0; box-sizing: border-box; }
  html, body { width: 1200px; height: 2673px; overflow: hidden; background: var(--page); }
  .screen {
    position: absolute; left: 0; top: 0;
    width: 360px; height: 802px;
    transform: scale(3.33334); transform-origin: 0 0;
    background: var(--page); overflow: hidden;
    font-family: "Titillium Web", sans-serif;
  }
  .topbar { position: absolute; left: 0; top: 0; width: 360px; height: 85px; background: var(--navy); }
  .cart-btn { position: absolute; left: 312px; top: 28px; width: 26px; height: 26px; }
  .cart-badge {
    position: absolute; left: 326px; top: 23px; width: 13px; height: 13px; border-radius: 50%;
    background: var(--accent); color: var(--white); font: 700 8px/13px "Lato", sans-serif; text-align: center;
  }
  .hero {
    position: absolute; left: 0; top: 85px; width: 360px; height: 177px;
    background: linear-gradient(180deg, #cfd6dc 0%, #7e8a7a 45%, #2c3a26 100%);
  }
  .chevron { position: absolute; left: 332px; width: 10px; height: 14px; }
  .product-card {
    position: absolute; left: 243px; width: 130px; height: 153px;
    background: var(--white); border: 1px solid var(--card-border); border-radius: 8px; overflow: hidden;
  }
  .product-thumb {
    position: absolute; left: 11px; top: 28px; width: 70px; height: 82px;
    background: var(--thumb); border-radius: 4px;
  }
  .product-title { position: absolute; left: 94px; top: 22px; font: 900 13px/16px "Lato", sans-serif; color: #111; }
  .product-desc { position: absolute; left: 94px; top: 58px; font: 400 10px/13px "Lato", sans-serif; color: #333; }
  .product-add { position: absolute; left: 96px; top: 127px; width: 44px; height: 44px; border-radius: 50%; background: var(--accent); }
  .scrim { position: absolute; inset: 0; background: var(--scrim); }

  .drawer { position: absolute; left: 0; top: 0; width: 235px; height: 802px; background: var(--white); }
  .drawer-close { position: absolute; left: 211px; top: 11px; width: 14px; height: 14px; }
  .menu { list-style: none; }
  .menu-item { position: absolute; left: 28px; display: flex; align-items: center; height: 24px; }
  .menu-icon { width: 20px; height: 20px; fill: var(--ink); }
  .menu-label { position: absolute; left: 41px; white-space: nowrap; font-weight: 700; font-size: 17px; color: var(--ink); }
  .copyright {
    position: absolute; left: 0; width: 235px; top: 770px; text-align: center;
    font: 900 8.5px/14px "Lato", sans-serif; color: #111;
  }
</style>
</head>
<body>
<div class="screen">
  <header class="topbar">
    <svg class="cart-btn" viewBox="0 0 24 24"><path fill="#8a93a3" d="M7 18a2 2 0 1 0 0 4 2 2 0 0 0 0-4zm10 0a2 2 0 1 0 0 4 2 2 0 0 0 0-4zM1 2v2h2l3.6 7.6-1.4 2.4A2 2 0 0 0 7 17h12v-2H7.4l1.1-2h7.5a2 2 0 0 0 1.7-1l3.6-6.5A1 1 0 0 0 20.4 4H5.2l-.9-2z"/></svg>
    <span class="cart-badge">1</span>
  </header>
  <div class="hero" role="img" aria-label="Palm trees against a pale sky"></div>

  <svg class="chevron" style="top:291px" viewBox="0 0 10 14"><path d="M2 1l6 6-6 6" stroke="#111" stroke-width="2" fill="none"/></svg>
  <article class="product-card" style="top:323px">
    <div class="product-thumb" role="img" aria-label="Grey graphic t-shirt"></div>
    <h3 class="product-title">Mid<br>Flyo</h3>
    <p class="product-desc">If yo<br>your<br>som<br>Labr</p>
    <span class="product-add"></span>
  </article>

  <svg class="chevron" style="top:522px" viewBox="0 0 10 14"><path d="M2 1l6 6-6 6" stroke="#111" stroke-width="2" fill="none"/></svg>
  <article class="product-card" style="top:555px">
    <div class="product-thumb" role="img" aria-label="Grey trucker cap with fish patch"></div>
    <h3 class="product-title">Bas</h3>
    <p class="product-desc" style="top:50px">Supe<br>struc<br>buck<br>profi</p>
    <span class="product-add"></span>
  </article>

  <svg class="chevron" style="top:751px" viewBox="0 0 10 14"><path d="M2 1l6 6-6 6" stroke="#111" stroke-width="2" fill="none"/></svg>
  <article class="product-card" style="top:782px"></article>

  <div class="scrim"></div>

  <nav class="drawer">
    <svg class="drawer-close" viewBox="0 0 14 14"><path d="M1 1l12 12M13 1L1 13" stroke="#0b1a33" stroke-width="2"/></svg>
    <ul class="menu">
      <li class="menu-item" style="top:47px">
        <svg class="menu-icon" viewBox="0 0 24 24"><path d="M12 3L2 12h3v9h5v-6h4v6h5v-9h3z"/></svg>
        <span class="menu-label">Home</span>
      </li>
      <li class="menu-item" style="top:110px">
        <svg class="menu-icon" viewBox="0 0 24 24"><path d="M7 18a2 2 0 1 0 0 4 2 2 0 0 0 0-4zm10 0a2 2 0 1 0 0 4 2 2 0 0 0 0-4zM1 2v2h2l3.6 7.6-1.4 2.4A2 2 0 0 0 7 17h12v-2H7.4l1.1-2h7.5a2 2 0 0 0 1.7-1l3.6-6.5A1 1 0 0 0 20.4 4H5.2l-.9-2z"/></svg>
        <span class="menu-label">My Cart</span>
      </li>
      <li class="menu-item" style="top:173px">
        <svg class="menu-icon" viewBox="0 0 24 24"><path d="M12 2a7 7 0 0 0-7 7c0 5.2 7 13 7 13s7-7.8 7-13a7 7 0 0 0-7-7zm0 9.5A2.5 2.5 0 1 1 12 6.5a2.5 2.5 0 0 1 0 5z"/></svg>
        <span class="menu-label">Track Oders</span>
      </li>
      <li class="menu-item" style="top:236px">
        <svg class="menu-icon" viewBox="0 0 24 24"><path d="M19.4 13a7.5 7.5 0 0 0 0-2l2.1-1.6-2-3.5-2.5 1a7 7 0 0 0-1.7-1L15 3h-4l-.4 2.7a7 7 0 0 0-1.7 1l-2.5-1-2 3.5L6.6 11a7.5 7.5 0 0 0 0 2l-2.1 1.6 2 3.5 2.5-1a7 7 0 0 0 1.7 1L11 21h4l.4-2.7a7 7 0 0 0 1.7-1l2.5 1 2-3.5zM13 15.5A3.5 3.5 0 1 1 13 8.5a3.5 3.5 0 0 1 0 7z" transform="translate(-1 0)"/></svg>
        <span class="menu-label" style="left:43px">Settings</span>
      </li>
      <li class="menu-item" style="top:302px">
        <svg class="menu-icon" viewBox="0 0 24 24"><circle cx="8" cy="7" r="4"/><path d="M0 21c0-4.4 3.6-7 8-7s8 2.6 8 7z"/><path d="M17 6h6v2h-6zM17 11h6v2h-6zM19 16h4v2h-4z"/></svg>
        <span class="menu-label">Contact</span>
      </li>
    </ul>
    <p class="copyright">© Pitchvale 2022</p>
  </nav>
</div>
</body>
</html>
```